QP Fiduciary Website Redesign Contest

We want to refresh our website to be more insitutional, professional for an international audience. We have designed a new logo for this purpose and that has been attached. A full brand brief and positioning statement has also been attached. Please read through all the documents carefully before designing. The old website is found here: https://qp-fiduciary.example/

Target Market(s)

Actuaries and associated businesses internationally

Industry/Entity Type

professional services - actuaries

Number of Pages Required

3 page

Font styles to use
Sans Serif

Colors
0054AA
0677BA
7BADD7
CADEEF
E8F1F8
0094D4
00A9DD
6FCCEA
C7EBF8
E9F6FB
F0912C
F2A743
F7CA91
FBE8D2
FDF5EE
EE7325
F08F49
F5BC92
FAE3D3
FDF4ED
EB3D1F
EC4F4E
F09395
F8D3D4
FCEDEE

Requirements
Must have
• blues and greens to match the logo color, complimentary colors, navigation
Nice to have
• old site: https://qp-fiduciary.example/

```html
<!DOCTYPE html>
<html lang="en">
<head>
<meta charset="utf-8">
<title>QP Fiduciary — Actuarial Software</title>
<link href="https://fonts.googleapis.com/css2?family=Montserrat:wght@600;700;800&family=Lato:wght@400;700&display=swap" rel="stylesheet">
<style>
:root{
  --navy:#0a1f55;
  --ink:#111827;
  --text:#2b3340;
  --blue:#0054aa;
  --blue-mid:#0677ba;
  --sky:#00a9dd;
  --pale:#e8f1f8;
  --green:#17896a;
  --green-dark:#0d6b52;
  --teal:#0f7a62;
  --grey-bg:#eef0f4;
  --white:#ffffff;
  --black:#050607;
}
*{box-sizing:border-box;margin:0;padding:0}
html,body{width:1200px;height:4728px;overflow:hidden}
body{position:relative;background:var(--white);font-family:"Lato",Arial,sans-serif;color:var(--text)}
.abs{position:absolute}
h1,h2,h3,h4{font-family:"Montserrat",Arial,sans-serif;color:var(--ink)}
.btn{position:absolute;display:flex;align-items:center;justify-content:center;background:var(--green);color:var(--white);
  font-family:"Lato",Arial,sans-serif;font-weight:700;font-size:16px;border-radius:24px;height:46px;text-decoration:none}
.center{left:0;width:1200px;text-align:center}

/* header */
.site-header{top:0;left:0;width:1200px;height:120px;background:var(--white)}
.brand{font-family:"Lato",Arial,sans-serif;font-weight:700;font-size:40px;color:var(--navy);letter-spacing:.5px}
.nav a{position:absolute;top:72px;font-size:17px;color:var(--ink);text-decoration:none}
.nav a.active{color:var(--blue);border-bottom:2px solid var(--blue);padding-bottom:4px}

/* hero */
.hero{top:120px;left:0;width:1200px;height:740px;background:linear-gradient(180deg,#04123a 0%,#0a2a7a 55%,#123fa6 100%)}
.hero-art{top:240px;left:0;width:1200px;height:420px;background:radial-gradient(ellipse at 50% 60%,rgba(60,150,255,.55),rgba(10,40,120,0) 70%)}
.hero h1{top:76px;color:var(--white);font-size:44px;line-height:54px;font-weight:800;letter-spacing:.3px}
.hero p{top:206px;left:200px;width:800px;color:var(--white);font-size:22px;line-height:32px;text-align:center}

/* capabilities intro */
.cap-photo{top:920px;left:112px;width:320px;height:380px;background:linear-gradient(135deg,#2c6fc9,#9cc8f0 55%,#1d4fa0)}
.section-title{font-size:36px;font-weight:800;text-transform:uppercase}
.cap-text{top:1030px;left:600px;width:480px;font-size:20px;line-height:30px}

/* green band */
.band{top:1340px;left:0;width:1200px;height:1260px;
  background:linear-gradient(180deg,#ffffff 0%,#cfe7dd 6%,#2e9c7d 14%,var(--teal) 40%,#0d6e58 100%)}
.tabs{top:1400px;left:112px;width:978px;height:76px}
.tab{position:absolute;top:0;height:76px;width:228px;border-radius:6px;display:flex;align-items:center;gap:12px;padding-left:20px;font-size:17px;color:var(--white);white-space:nowrap}
.tab i{display:block;flex:none;width:22px;height:22px;border:2px solid currentColor;border-radius:4px}
.core-title{top:1700px;color:var(--white);font-size:40px;font-weight:800}
.core-text{top:1855px;left:170px;width:860px;color:var(--white);font-size:20px;line-height:30px;text-align:center}
.card{position:absolute;top:1952px;width:320px;height:368px;background:var(--white);border-radius:12px;text-align:center}
.card .icon{margin:28px auto 0;width:72px;height:72px;border-radius:50%;background:var(--blue-mid);display:flex;align-items:center;justify-content:center}
.card h3{margin-top:22px;font-size:19px;font-weight:700;white-space:nowrap}
.card p{margin:14px auto 0;width:260px;font-size:15px;line-height:22px}
.card .btn{left:90px;top:290px;width:140px}

/* process */
.step{position:absolute;top:2842px;width:240px;text-align:center}
.step .num{margin:0 auto;width:76px;height:76px;border-radius:50%;background:var(--blue);color:var(--white);
  font-family:"Montserrat",Arial,sans-serif;font-size:30px;font-weight:700;display:flex;align-items:center;justify-content:center;border:5px solid #ffffff;box-shadow:0 0 0 3px var(--blue)}
.step h4{margin-top:20px;font-size:18px;font-weight:700;white-space:nowrap}
.step p{margin:6px auto 0;width:210px;font-size:15px;line-height:21px}
.step.accent .num{background:var(--green);box-shadow:0 0 0 3px var(--green)}
.step.accent h4{color:var(--green)}

/* insights */
.ins-text{top:3336px;left:108px;width:500px;font-size:21px;line-height:30px}
.bullets{top:3410px;left:108px;width:500px;list-style:none}
.bullets li{position:relative;padding-left:30px;font-size:18px;line-height:27px;margin-bottom:16px}
.bullets li::before{content:"";position:absolute;left:0;top:8px;width:12px;height:12px;border-radius:50%;background:var(--blue)}
.ins-photo{top:3268px;left:652px;width:436px;height:392px;border-radius:16px;background:linear-gradient(135deg,#04123a 20%,#1659c8 60%,#5aa6ff 75%,#061a52 95%)}

/* cta */
.cta{top:3700px;left:0;width:1200px;height:340px;background:linear-gradient(180deg,#ffffff,#f1f2f5)}
.cta-sub{top:3840px;left:220px;width:760px;font-size:21px;line-height:31px;text-align:center}

/* footer */
.footer{top:4240px;left:0;width:1200px;height:488px;background:var(--black);color:var(--white)}
.footer h4{position:absolute;top:140px;font-family:"Lato",Arial,sans-serif;color:var(--white);font-size:22px;font-weight:700}
.footer ul{position:absolute;top:190px;list-style:none}
.footer li{font-size:15px;line-height:20px;margin-bottom:18px;color:#e9ecf0}
.about{position:absolute;top:188px;left:108px;width:200px;font-size:15px;line-height:22px;color:#e9ecf0}
.contact-row{position:absolute;left:868px;display:flex;gap:18px;font-size:14px;line-height:20px;width:260px}
.social{position:absolute;top:352px;left:108px;display:flex;gap:14px}
.social span{width:30px;height:30px;border-radius:50%;background:#2e3238}
.social span:first-child{background:var(--green)}
.copyright{position:absolute;top:462px;left:0;width:1200px;text-align:center;font-size:13px;color:#cfd3d8}
</style>
</head>
<body>

<header class="site-header abs">
  <div class="brand abs" style="left:40px;top:30px;">QP Fiduciary</div>
  <a class="btn" style="left:820px;top:10px;width:270px;" href="#">Request Technical Walkthrough</a>
  <nav class="nav">
    <a class="active" style="left:530px;" href="#">Home</a>
    <a style="left:614px;" href="#">Platform</a>
    <a style="left:720px;" href="#">Solutions</a>
    <a style="left:828px;" href="#">Insights</a>
    <a style="left:922px;" href="#">Company</a>
    <a style="left:1036px;" href="#">Contact</a>
  </nav>
</header>

<section class="hero abs">
  <div class="hero-art abs" role="img" aria-label="Abstract flowing blue data wave"></div>
  <h1 class="abs center">ACTUARIAL SOFTWARE FOR STRUCTURED,<br>AUDITABLE FINANCIAL ANALYSIS</h1>
  <p class="abs">Software that translates actuarial methodologies into disciplined decision-ready analytical tools across diverse regulatory environments.</p>
  <a class="btn" style="left:455px;top:300px;width:290px;" href="#">Request Technical Walkthrough</a>
  <svg class="abs" style="left:0;top:580px" width="1200" height="170" viewBox="0 0 1200 170">
    <path d="M0 40 Q600 210 1200 40 L1200 170 L0 170Z" fill="#ffffff"/>
    <path d="M0 30 Q600 200 1200 20" fill="none" stroke="#1f6fd8" stroke-width="14"/>
    <path d="M0 58 Q600 220 1200 50" fill="none" stroke="#8fc1f0" stroke-width="3"/>
  </svg>
</section>

<div class="cap-photo abs" role="img" aria-label="Glass office tower viewed from below against the sky"></div>
<h2 class="section-title abs" style="left:600px;top:960px;">Platform Capabilities</h2>
<div class="abs" style="left:600px;top:1010px;width:470px;height:2px;background:#d7dce3"></div>
<p class="cap-text abs">QP Fiduciary develops modular actuarial software designed to support reserving, valuation, pricing, and risk analysis workflows across diverse regulatory environments.</p>
<a class="btn" style="left:600px;top:1200px;width:184px;" href="#">Explore Platform</a>

<section class="band abs" role="img" aria-label="Green toned city skyline backdrop"></section>
<div class="tabs abs">
  <div class="tab" style="left:0;background:#c9d3e4;color:#1f3b7a;"><i></i>Data Inputs</div>
  <div class="tab" style="left:250px;background:#3f59b5;"><i></i>Actuarial Models</div>
  <div class="tab" style="left:500px;background:#5f8fa0;"><i></i>Structured Analysis</div>
  <div class="tab" style="left:750px;background:#4e8a86;"><i></i>Review</div>
</div>
<h2 class="core-title abs center">CORE SOLUTIONS</h2>
<p class="core-text abs">QP Fiduciary develops modular actuarial software designed to support reserving, valuation, pricing, and risk analysis workflows across diverse regulatory environments.</p>

<div class="card" style="left:100px;">
  <div class="icon"><svg width="36" height="36" viewBox="0 0 36 36" fill="none" stroke="#fff" stroke-width="3"><rect x="6" y="8" width="24" height="20" rx="2"/><path d="M11 22v-6M18 22V12M25 22v-8"/></svg></div>
  <h3>Reserving &amp; Valuation</h3>
  <p>Software supporting structured reserving workflows and financial reporting across jurisdictions.</p>
  <a class="btn" href="#">Read More</a>
</div>
<div class="card" style="left:440px;">
  <div class="icon"><svg width="36" height="36" viewBox="0 0 36 36" fill="none" stroke="#fff" stroke-width="3"><circle cx="18" cy="18" r="11"/><path d="M18 11v14M14 15h6a3 3 0 0 1 0 6h-6"/></svg></div>
  <h3>Pricing</h3>
  <p>Models supporting insurance and reinsurance pricing based on actuarial methodologies.</p>
  <a class="btn" href="#">Read More</a>
</div>
<div class="card" style="left:776px;">
  <div class="icon"><svg width="36" height="36" viewBox="0 0 36 36" fill="none" stroke="#fff" stroke-width="3"><path d="M18 5l11 5v8c0 7-5 11-11 13C12 29 7 25 7 18v-8z"/><path d="M13 18l4 4 7-8"/></svg></div>
  <h3>Enterprise Risk Management</h3>
  <p>Software supporting reinsurance optimization, capital modeling, and risk assessment for decision-making.</p>
  <a class="btn" href="#">Read More</a>
</div>

<svg class="abs" style="left:0;top:2380px" width="1200" height="860" viewBox="0 0 1200 860">
  <path d="M0 120 Q600 -40 1200 120 L1200 760 Q600 880 0 760Z" fill="#eef0f4"/>
  <path d="M0 120 Q600 -40 1200 120" fill="none" stroke="#ffffff" stroke-width="16"/>
</svg>
<h2 class="section-title abs center" style="top:2570px;">Platform Capabilities</h2>
<p class="abs" style="top:2650px;left:220px;width:760px;font-size:21px;line-height:31px;text-align:center;">Designed to support disciplined actuarial analysis through structured workflows, transparent assumptions, and governance-ready outputs</p>
<div class="abs" style="left:220px;top:2879px;width:760px;height:3px;background:var(--blue)"></div>
<div class="step" style="left:100px;"><div class="num">01</div><h4>Structured Workflows</h4><p>Structured workflows suitable for multi-jurisdictional review</p></div>
<div class="step" style="left:352px;"><div class="num">02</div><h4>Transparent Assumptions</h4><p>Transparent assumptions and methodological clarity</p></div>
<div class="step accent" style="left:604px;"><div class="num">03</div><h4>Scenario Analysis</h4><p>Evaluate multiple scenarios to support informed decisions</p></div>
<div class="step" style="left:860px;"><div class="num">04</div><h4>Professional Judgment</h4><p>Supports professional judgment rather than replacing it</p></div>
<a class="btn" style="left:507px;top:3086px;width:186px;" href="#">Discover Platform</a>

<h2 class="section-title abs" style="left:108px;top:3270px;">Insights</h2>
<p class="ins-text abs">Practitioner perspectives on actuarial methodology, governance, and financial analysis.</p>
<ul class="bullets abs">
  <li>Methodological perspectives in actuarial reserving</li>
  <li>Governance considerations in multi-jurisdictional analysis</li>
  <li>Observations on actuarial practice in emerging markets</li>
</ul>
<a class="btn" style="left:108px;top:3600px;width:160px;" href="#">Read Insights</a>
<div class="ins-photo abs" role="img" aria-label="Abstract glowing blue ribbon shapes on a dark background"></div>

<section class="cta abs"></section>
<h2 class="abs center" style="top:3760px;font-size:34px;font-weight:800;">INTERESTED IN EXPLORING THE PLATFORM?</h2>
<p class="cta-sub abs">Designed to support disciplined actuarial analysis through structured workflows, transparent assumptions, and governance-ready outputs</p>
<a class="btn" style="left:455px;top:3950px;width:290px;" href="#">Request Technical Walkthrough</a>

<svg class="abs" style="left:0;top:4040px" width="1200" height="210" viewBox="0 0 1200 210">
  <rect width="1200" height="210" fill="#e9ebef"/>
  <path d="M0 60 Q500 180 1200 80 L1200 210 L0 210Z" fill="#cdd1d8"/>
  <path d="M0 120 Q600 240 1200 110 L1200 210 L0 210Z" fill="#9aa0aa"/>
  <path d="M0 150 Q600 250 1200 150 L1200 210 L0 210Z" fill="#050607"/>
  <path d="M0 138 Q600 250 1200 130" fill="none" stroke="#1f6fd8" stroke-width="10"/>
</svg>

<footer class="footer abs">
  <div class="brand abs center" style="top:28px;color:#ffffff;">QP Fiduciary</div>
  <h4 style="left:108px;">About Us</h4>
  <p class="about">QP Fiduciary develops actuarial software for structured, transparent financial analysis across reserving, pricing and risk management.</p>
  <div class="social"><span></span><span></span><span></span></div>
  <h4 style="left:456px;">Main Links</h4>
  <ul style="left:456px;"><li>Home</li><li>Company</li><li>Platform</li><li>Solutions</li><li>Insights</li></ul>
  <h4 style="left:648px;">Other Links</h4>
  <ul style="left:648px;"><li>Contact</li><li>Blog</li><li>Privacy Policy</li><li>Terms of Service</li><li>Legal Mentions</li></ul>
  <h4 style="left:868px;">Contact Us</h4>
  <div class="contact-row" style="top:192px;">
    <svg width="18" height="22" viewBox="0 0 18 22" fill="none" stroke="#fff" stroke-width="2"><path d="M9 21s7-7 7-12A7 7 0 0 0 2 9c0 5 7 12 7 12z"/><circle cx="9" cy="9" r="2.5"/></svg>
    <span>480 Harbor Crest Ave,<br>Suite 210 Lakemont, FL<br>30000</span>
  </div>
  <div class="contact-row" style="top:276px;">
    <svg width="18" height="18" viewBox="0 0 18 18" fill="none" stroke="#fff" stroke-width="2"><path d="M4 1l3 4-2 2a10 10 0 0 0 6 6l2-2 4 3-2 3C8 17 1 10 1 3z"/></svg>
    <span>+1 (555) 010-4826</span>
  </div>
  <div class="contact-row" style="top:326px;">
    <svg width="20" height="16" viewBox="0 0 20 16" fill="none" stroke="#fff" stroke-width="2"><rect x="1" y="1" width="18" height="14" rx="1"/><path d="M1 2l9 7 9-7"/></svg>
    <span>admin@qp-fiduciary.example</span>
  </div>
  <p class="copyright">Copyright © 2026 QP Fiduciary. All rights reserved.</p>
</footer>

</body>
</html>
```